Boutique custom software development company needs new business card

Our nearly 20 year old custom software development company would like to better include the fact that we are now providing Bitcoin services. These new services are B2B include education (how to acquire and securely hold Bitcoin) and integrating Bitcoin payments into existing ecommerce sites or other existing systems. Please keep the card clean and simple. Attached is our current design and some other files. vextorial.com

Target Market(s)

businesses owners interested in long term relationship

Industry/Entity Type

Custom software development and Bitcoin

Contact Information for Business Card

Dale Parker, dale@vextorial.com, vextorial.com, (888) 555-VXTRL

Font styles to use
Other font styles liked:
• monospace

Requirements
Must have
• double-sided
Nice to have
• clean and simple
Should not have
• physical address

```html
<!DOCTYPE html>
<html lang="en">
<head>
<meta charset="utf-8">
<title>Vextorial Business Card</title>
<link rel="stylesheet" href="https://fonts.googleapis.com/css2?family=Montserrat:wght@400;500;800&display=swap">
<style>
  :root {
    --page: #e4e4e4;
    --card: #d8e2ee;
    --brand-blue: #3d74bd;
    --brand-orange: #f07f22;
    --pale-blue: #b8cce4;
    --pale-sand: #e0d2c8;
    --ink: #3a3a3a;
  }
  * { margin: 0; padding: 0; box-sizing: border-box; }
  html, body { width: 1200px; height: 900px; overflow: hidden; }
  body {
    background: var(--page);
    font-family: "Montserrat", sans-serif;
    display: flex;
    flex-direction: column;
    align-items: center;
    justify-content: center;
    gap: 50px;
  }
  .card {
    position: relative;
    width: 620px;
    height: 360px;
    background: var(--card);
    border-radius: 22px;
    overflow: hidden;
    box-shadow: 0 3px 10px rgba(0,0,0,0.18);
  }
  .wordmark {
    font-weight: 800;
    color: var(--brand-blue);
    letter-spacing: -0.5px;
    line-height: 1;
  }
  .tagline {
    font-weight: 500;
    color: var(--brand-blue);
    white-space: nowrap;
  }
  .card-front {
    display: flex;
    align-items: center;
    justify-content: center;
  }
  .card-front .brand { display: flex; flex-direction: column; align-items: flex-start; }
  .card-front .wordmark { font-size: 84px; }
  .card-front .tagline { font-size: 20px; margin-top: 8px; }

  .corner-block {
    position: absolute;
    top: 0;
    right: 0;
    width: 260px;
    height: 180px;
  }
  .card-back .brand {
    position: absolute;
    left: 48px;
    top: 60px;
  }
  .card-back .wordmark { font-size: 48px; }
  .card-back .tagline { font-size: 13px; margin-top: 5px; }
  .person {
    position: absolute;
    left: 48px;
    top: 196px;
  }
  .person-name {
    font-weight: 800;
    font-size: 26px;
    letter-spacing: 1.5px;
    line-height: 1.1;
    text-transform: uppercase;
  }
  .person-name .first { color: var(--brand-orange); }
  .person-name .last { color: var(--brand-blue); }
  .person-title {
    font-size: 17px;
    color: var(--ink);
    margin-top: 2px;
  }
  .divider {
    position: absolute;
    left: 48px;
    right: 48px;
    top: 272px;
    height: 1px;
    background: var(--brand-orange);
  }
  .contacts {
    position: absolute;
    left: 48px;
    right: 48px;
    top: 288px;
    display: flex;
    align-items: center;
    gap: 9px;
    font-size: 14px;
    color: var(--ink);
    white-space: nowrap;
  }
  .contact { display: flex; align-items: center; gap: 6px; }
  .contact svg { width: 13px; height: 13px; fill: var(--brand-blue); }
  .sep { color: var(--brand-orange); }
</style>
</head>
<body>
  <section class="card card-front">
    <div class="brand">
      <div class="wordmark">Vextorial</div>
      <div class="tagline">custom applications &amp; bitcoin services</div>
    </div>
  </section>

  <section class="card card-back">
    <svg class="corner-block" viewBox="0 0 260 180" aria-hidden="true">
      <polygon points="70,0 260,0 260,110 150,180" fill="var(--pale-blue)"/>
      <polygon points="110,150 170,150 150,180 120,180" fill="var(--pale-sand)"/>
    </svg>
    <div class="brand">
      <div class="wordmark">Vextorial</div>
      <div class="tagline">custom applications &amp; bitcoin services</div>
    </div>
    <div class="person">
      <div class="person-name"><span class="first">Dale</span> <span class="last">Parker</span></div>
      <div class="person-title">Owner</div>
    </div>
    <div class="divider"></div>
    <div class="contacts">
      <span class="contact">
        <svg viewBox="0 0 24 24" aria-hidden="true"><path d="M6.6 10.8a15.1 15.1 0 0 0 6.6 6.6l2.2-2.2c.3-.3.7-.4 1-.2 1.1.4 2.3.6 3.6.6.6 0 1 .4 1 1V20c0 .6-.4 1-1 1A17 17 0 0 1 3 4c0-.6.4-1 1-1h3.5c.6 0 1 .4 1 1 0 1.3.2 2.5.6 3.6.1.3 0 .7-.2 1z"/></svg>
        (888) 555-VXTRL
      </span>
      <span class="sep">|</span>
      <span class="contact">
        <svg viewBox="0 0 24 24" aria-hidden="true"><path d="M2 5h20v14H2z"/><path d="M3 6l9 7 9-7" fill="none" stroke="#d8e2ee" stroke-width="1.6"/></svg>
        dale@vextorial.com
      </span>
      <span class="sep">|</span>
      <span class="contact">
        <svg viewBox="0 0 24 24" aria-hidden="true"><circle cx="12" cy="12" r="10"/><path d="M2 12h20M12 2c3 3 3 17 0 20M12 2c-3 3-3 17 0 20" fill="none" stroke="#d8e2ee" stroke-width="1.4"/></svg>
        www.vextorial.com
      </span>
    </div>
  </section>
</body>
</html>
```